Concise,Good colour matching,Good looks design for "HERD SCAN QUICK ASSAY FOR LIVESTOCK"

Product Positioning: Affordable test for Large Animals (Livestock/Veterinary Use)
Product Name: HERD SCAN Quick Assay Kit (for large animals, e.g., cattle, horses, swine,Avian,sheep).

2. Packaging Requirements

A. Visual Design
Color Scheme:
Green/Blue/Orange/Yellow/Red/Gray/White(chose 2~4 colors)

Mandatory Info:
Brand logo ("HERD SCAN")

Target Market(s)

Southeast Asia, Africa, Middle East, South America

Industry/Entity Type

Veterinary diagnostic for LIVESTOCK

Colors

Designer to choose colors to be used in the design.

Requirements
Nice to have
• Concise,Good colour matching,Good looks

```html
<!DOCTYPE html>
<html lang="en">
<head>
<meta charset="utf-8">
<title>HERD SCAN Quick Assay Kit – Packaging</title>
<link href="https://fonts.googleapis.com/css2?family=Montserrat:wght@700;800&family=Open+Sans:wght@400;700&display=swap" rel="stylesheet">
<style>
  :root {
    --navy: #0b2a78;
    --green: #17a02b;
    --green-deep: #0d5a18;
    --green-mid: #2d8a32;
    --green-light: #7cc67a;
    --white: #ffffff;
    --stage: #f2f3f5;
  }
  * { margin: 0; padding: 0; box-sizing: border-box; }
  html, body { width: 1200px; height: 800px; overflow: hidden; background: var(--stage); }
  .canvas { position: relative; width: 1200px; height: 800px; }

  .panel { position: absolute; overflow: hidden; }

  /* Lid */
  .lid { left: 300px; top: 30px; width: 640px; height: 420px; background: var(--navy); }
  .photo-grid {
    position: absolute; left: 0; top: 0; width: 640px; height: 270px;
    display: grid; grid-template-columns: repeat(3, 1fr); grid-template-rows: repeat(2, 1fr);
  }
  .photo { width: 100%; height: 100%; }
  .photo--a { background: linear-gradient(135deg, var(--green-mid), var(--green-deep)); }
  .photo--b { background: linear-gradient(160deg, var(--green-light), var(--green-mid)); }
  .photo--c { background: linear-gradient(200deg, #0a3a10, var(--green-mid)); }
  .photo--d { background: linear-gradient(120deg, var(--green-light), var(--green-deep)); }
  .photo--e { background: linear-gradient(150deg, var(--green-deep), var(--green-light)); }
  .photo--f { background: linear-gradient(110deg, var(--green-mid), #3fa541); }

  .tagline {
    position: absolute; left: 36px; top: 290px;
    font-family: "Montserrat", sans-serif; font-weight: 700; font-size: 22px; line-height: 1.15;
    color: var(--white);
  }
  .lid-strip {
    position: absolute; left: 0; bottom: 0; width: 640px; height: 60px; background: var(--white);
  }
  .lid-strip .notch { position: absolute; left: 300px; top: -1px; }
  .lid-strip .brand {
    position: absolute; right: 36px; top: 13px;
    font-family: "Montserrat", sans-serif; font-weight: 800; font-size: 28px; letter-spacing: 1px;
    color: var(--navy);
  }

  /* Front */
  .front { left: 300px; top: 450px; width: 640px; height: 330px; background: var(--navy); text-align: center; }
  .front .brand-row { margin-top: 76px; display: flex; justify-content: center; align-items: center; gap: 14px; }
  .brand-mark { width: 22px; height: 22px; background: var(--green); }
  .front .brand {
    font-family: "Montserrat", sans-serif; font-weight: 800; font-size: 52px; letter-spacing: 2px;
    color: var(--white);
  }
  .front .info {
    margin-top: 18px;
    font-family: "Open Sans", sans-serif; font-weight: 700; font-size: 15px; line-height: 1.5;
    color: var(--white);
  }

  /* Side */
  .side {
    left: 40px; top: 450px; width: 260px; height: 330px; background: var(--navy);
    padding: 26px 24px 24px; display: flex; flex-direction: column;
  }
  .side .label {
    font-family: "Montserrat", sans-serif; font-weight: 700; font-size: 24px; line-height: 1.2;
    color: var(--green); letter-spacing: 0.5px;
  }
  .features { margin-top: 12px; list-style: none; }
  .features li {
    font-family: "Open Sans", sans-serif; font-size: 11px; line-height: 1.4; color: var(--white);
    margin-bottom: 8px;
  }
  .features li:last-child { margin-bottom: 0; }
  .features strong { font-weight: 700; }
  .side .brand {
    margin-top: auto; padding-top: 10px;
    font-family: "Montserrat", sans-serif; font-weight: 800; font-size: 28px; line-height: 1.1;
    letter-spacing: 1px; color: var(--white);
  }
</style>
</head>
<body>
<main class="canvas">

  <section class="panel lid">
    <div class="photo-grid">
      <div class="photo photo--a" role="img" aria-label="Green-toned photo of a horse in a field"></div>
      <div class="photo photo--b" role="img" aria-label="Green-toned photo of a cow on pasture"></div>
      <div class="photo photo--c" role="img" aria-label="Green-toned photo of a rooster"></div>
      <div class="photo photo--d" role="img" aria-label="Green-toned photo of a pig"></div>
      <div class="photo photo--e" role="img" aria-label="Green-toned photo of a white duck on grass"></div>
      <div class="photo photo--f" role="img" aria-label="Green-toned photo of sheep grazing"></div>
    </div>
    <p class="tagline">Affordable Diagnostics<br>for Healthy Herds</p>
    <div class="lid-strip">
      <svg class="notch" width="40" height="22" viewBox="0 0 40 22" aria-hidden="true">
        <path d="M0 0 A20 20 0 0 0 40 0 Z" fill="#dfe2e8"/>
      </svg>
      <span class="brand">HERD SCAN</span>
    </div>
  </section>

  <section class="panel side">
    <h2 class="label">RAPID TEST</h2>
    <ul class="features">
      <li><strong>Fast &amp; Efficient:</strong> Rapid test results in less than 10 minutes from prep to completion.</li>
      <li><strong>Affordable:</strong> Colloidal gold-based rapid tests that combine high accuracy with cost-effectiveness.</li>
      <li><strong>Reliable &amp; Simple:</strong> Stable test performance with 2-30 °C. Easy to operate, no professional skills required.</li>
    </ul>
    <span class="brand">HERD SCAN</span>
  </section>

  <section class="panel front">
    <div class="brand-row">
      <span class="brand-mark" aria-hidden="true"></span>
      <h1 class="brand">HERD SCAN</h1>
    </div>
    <p class="info">
      Manufactured by FIELDMARK<br>
      Storage: 2-30 °C, Do not freeze<br>
      See the instructions for other contents
    </p>
  </section>

</main>
</body>
</html>
```